Financial Advisor Resource Firm needs business card design

Need business card design for company in Omaha NE called Meridale Circle. We provide resources to financial advisors....workshop programs, retirement analysis, and insurance planning. I would like to see designs that use grays, greens, black, and white colors. The final design should communicate 'collaboration' and be simple yet attractive to financial planning clients. I will attached our logo and another picture of a puzzle piece coming together. I would like the incorporate the puzzle picture somehow, maybe on the back somehow, with color or just the gray scale....OR, the picture be the front of the card with 'Meridale' definition on it (see upload) and then company logo, employee name, title, address on the back (see ppt uploaded). The following disclosure needs to be included somewhere- Advisory services offered through Stonebrook Assets, LLC.
Updates

I uploaded a svg and ai file of the logo

Target Market(s)

Financial planning clients and financial advisors....so pretty diverse age range of about 40-70.

Industry/Entity Type

Financial Planning

Contact Information for Business Card

Tobias L. Fenwright, MBA
Founder/President
5287 E. Larkin Road
Suite 230
Omaha, NE 68190
Phone- (402) 555-0147
Cell- (402) 555-0183
Fax- (402) 555-0129
email- tobias@meridaleplan.example
web address- www.meridaleplan.example

Colors
1b1b1b
474747
d3d3d3
ffffff
9bcb3c
abd036

Requirements
Must have
• Must include logo provided, must be 2 sided, and must have disclosure...all of these items listed in project description

```html
<!DOCTYPE html>
<html lang="en">
<head>
<meta charset="utf-8">
<title>Meridale Circle business card</title>
<link href="https://fonts.googleapis.com/css2?family=Cinzel:wght@500;700&family=Crimson+Text:wght@400&family=Montserrat:wght@400;500&family=Open+Sans:wght@400&display=swap" rel="stylesheet">
<style>
  :root {
    --ink: #1b1b1b;
    --slate: #474747;
    --mist: #d3d3d3;
    --paper: #ffffff;
    --leaf: #9bcb3c;
    --lime: #abd036;
    --ground: #2a2a2a;
  }
  * { box-sizing: border-box; margin: 0; padding: 0; }
  html, body { width: 1200px; height: 900px; overflow: hidden; }
  body {
    background: var(--ground);
    display: flex; flex-direction: column; align-items: center; justify-content: center;
    gap: 48px;
  }
  .card {
    position: relative;
    width: 660px; height: 377px;
    background: var(--paper);
    overflow: hidden;
    box-shadow: 0 12px 30px rgba(0,0,0,.45);
  }

  /* front */
  .front .brand {
    position: absolute; left: 0; right: 0; top: 140px;
    display: flex; align-items: center; justify-content: center; gap: 14px;
  }
  .front .brand-dot {
    width: 30px; height: 30px; border-radius: 50%;
    border: 4px solid var(--leaf);
  }
  .front .brand-name {
    font-family: "Cinzel", serif; font-weight: 700;
    font-size: 44px; letter-spacing: 1px; color: var(--ink);
  }
  .front .rule-top {
    position: absolute; right: 0; top: 110px; width: 170px; height: 3px; background: var(--lime);
  }
  .front .web-row {
    position: absolute; left: 0; right: 0; top: 255px;
    display: flex; align-items: center; gap: 18px;
  }
  .front .rule-bottom { width: 190px; height: 3px; background: var(--lime); }
  .front .web {
    font-family: "Open Sans", sans-serif; font-size: 16px; letter-spacing: 4px; color: var(--ink);
  }

  /* back */
  .back .photo { position: absolute; inset: 0; width: 100%; height: 100%; }
  .back .definition {
    position: absolute; left: 80px; top: 56px; width: 300px;
    color: var(--paper);
  }
  .back .word {
    font-family: "Cinzel", serif; font-size: 40px; color: var(--leaf);
    font-weight: 500; letter-spacing: 1px; line-height: 1.1;
  }
  .back .phonetic {
    font-family: "Crimson Text", serif; font-size: 24px; line-height: 1.1;
    margin: 2px 0 8px 90px;
  }
  .back .meaning {
    font-family: "Montserrat", sans-serif; font-size: 13.5px; line-height: 1.4;
  }
  .back .faint-name {
    position: absolute; left: 34px; top: 200px;
    font-family: "Cinzel", serif; font-weight: 700; font-size: 34px;
    color: rgba(255,255,255,.12); white-space: nowrap;
  }
  .back .contact {
    position: absolute; right: 32px; top: 138px;
    font-family: "Open Sans", sans-serif; font-size: 14.5px; color: var(--ink);
    text-align: right; line-height: 1.55;
  }
  .back .contact li { list-style: none; display: flex; justify-content: flex-end; align-items: center; gap: 10px; }
  .back .contact svg { width: 14px; height: 14px; fill: var(--leaf); }
  .back .contact .address { margin-top: 2px; padding-right: 24px; display: block; }
  .back .person { position: absolute; left: 60px; bottom: 40px; }
  .back .person-name {
    font-family: "Cinzel", serif; font-weight: 700; font-size: 20px; color: var(--slate);
  }
  .back .person-title {
    font-family: "Montserrat", sans-serif; font-size: 18px; color: var(--leaf);
  }
  .back .disclosure {
    position: absolute; right: 32px; bottom: 14px;
    font-family: "Open Sans", sans-serif; font-size: 10px; color: var(--slate);
  }
</style>
</head>
<body>

<section class="card front">
  <div class="rule-top"></div>
  <div class="brand">
    <span class="brand-dot"></span>
    <span class="brand-name">Meridale Circle</span>
  </div>
  <div class="web-row">
    <span class="rule-bottom"></span>
    <span class="web">www.meridaleplan.example</span>
  </div>
</section>

<section class="card back">
  <svg class="photo" viewBox="0 0 660 377" preserveAspectRatio="none" role="img" aria-label="Grayscale photo of hands fitting puzzle pieces together">
    <defs>
      <linearGradient id="photoTone" x1="0" y1="1" x2="1" y2="0">
        <stop offset="0" stop-color="#3c3c3c"/>
        <stop offset=".5" stop-color="#8a8a8a"/>
        <stop offset="1" stop-color="#5a5a5a"/>
      </linearGradient>
    </defs>
    <polygon points="0,0 660,0 660,120 400,120 365,265 0,265" fill="url(#photoTone)"/>
  </svg>

  <div class="faint-name">Meridale Circle</div>

  <div class="definition">
    <div class="word">MERIDALE</div>
    <div class="phonetic">mer'i·dāl</div>
    <p class="meaning">: to come together and unite in common interest and focus</p>
  </div>

  <ul class="contact">
    <li>(402) 555-0147
      <svg viewBox="0 0 24 24"><path d="M6.6 10.8a15 15 0 0 0 6.6 6.6l2.2-2.2a1 1 0 0 1 1-.25 11.4 11.4 0 0 0 3.6.6 1 1 0 0 1 1 1V20a1 1 0 0 1-1 1A17 17 0 0 1 3 4a1 1 0 0 1 1-1h3.5a1 1 0 0 1 1 1c0 1.250.2 2.450.6 3.6a1 1 0 0 1-.25 1z"/></svg></li>
    <li>(402) 555-0183
      <svg viewBox="0 0 24 24"><path d="M7 1h10a2 2 0 0 1 2 2v18a2 2 0 0 1-2 2H7a2 2 0 0 1-2-2V3a2 2 0 0 1 2-2zm0 3v15h10V4z"/></svg></li>
    <li>(402) 555-0129
      <svg viewBox="0 0 24 24"><path d="M6 2h9l3 3v4h2a2 2 0 0 1 2 2v9a2 2 0 0 1-2 2H4a2 2 0 0 1-2-2v-9a2 2 0 0 1 2-2h2zm2 2v5h8V6h-2V4zm-2 9v2h3v-2zm5 0v2h3v-2z"/></svg></li>
    <li>tobias@meridaleplan.example
      <svg viewBox="0 0 24 24"><path d="M2 5h20v14H2zm2 2v.5l8 5 8-5V7z"/></svg></li>
    <li class="address">5287 E. Larkin Road, Suite 230<br>Omaha, NE 68190</li>
  </ul>

  <div class="person">
    <div class="person-name">TOBIAS L. FENWRIGHT, MBA</div>
    <div class="person-title">Founder/President</div>
  </div>

  <p class="disclosure">Advisory services offered through Stonebrook Assets, LLC.</p>
</section>

</body>
</html>
```